Harborline Renewal Business Card Design

Professional and clean design. The design colors should flow with the logo. Two-sided card with the website on the back which is:

www.HarborlineRenewal.example.

"Specializing in Water Damage Restoration"

On the front I need the name, email, phone, and logo.

Name: Darnell Quisby
Email: Darnell@HarborlineRenewal.example
Phone: 555-318-2046 for now

I only have the Preview and Thumbnail right now but should have the source files uploaded within a day or two.

Target Market(s)

Flood victims, home owners with water damage from busted pipes etc...

Industry/Entity Type

Business

Contact Information for Business Card

Name: Darnell Quisby

Font styles to use
Serif
Sans Serif

Requirements
Must have
• Business Card Details Info

```html
<!DOCTYPE html>
<html lang="en">
<head>
<meta charset="utf-8">
<title>Harborline Renewal — Business Card</title>
<link rel="stylesheet" href="https://fonts.googleapis.com/css2?family=Cinzel:wght@400;600&family=Open+Sans:wght@400;600&display=swap">
<style>
  :root {
    --stage: #e8edf1;
    --blue-light: #3cc3e6;
    --blue-mid: #23a8d8;
    --blue-deep: #1787c4;
    --paper: #f7f8f9;
    --ink-blue: #1f9fd6;
    --white: #ffffff;
    --soft-line: rgba(255, 255, 255, 0.75);
  }
  * { box-sizing: border-box; margin: 0; padding: 0; }
  html, body { width: 1200px; height: 780px; overflow: hidden; }
  body {
    background: var(--stage);
    display: flex;
    align-items: center;
    justify-content: center;
    gap: 40px;
    font-family: "Open Sans", sans-serif;
  }
  .card {
    width: 540px;
    height: 309px;
    position: relative;
    overflow: hidden;
    box-shadow: 0 10px 26px rgba(20, 60, 90, 0.18);
  }
  .blue-field {
    background: radial-gradient(circle at 45% 40%, var(--blue-light) 0%, var(--blue-mid) 55%, var(--blue-deep) 100%);
  }
  .faint-ring {
    position: absolute;
    border-radius: 50%;
    border: 22px solid rgba(255, 255, 255, 0.08);
  }

  /* Front */
  .card-front { display: flex; }
  .front-brand {
    width: 42%;
    background: var(--paper);
    display: flex;
    flex-direction: column;
    align-items: center;
    justify-content: center;
    gap: 10px;
    color: var(--ink-blue);
    border-right: 4px solid var(--blue-light);
  }
  .brand-dot {
    width: 42px; height: 42px; border-radius: 50%;
    background: var(--ink-blue);
  }
  .brand-name {
    font-family: "Cinzel", serif;
    font-weight: 600;
    font-size: 25px;
    letter-spacing: 1px;
    line-height: 1;
  }
  .brand-sub {
    font-family: "Cinzel", serif;
    font-size: 11px;
    letter-spacing: 6px;
    display: flex; align-items: center; gap: 6px;
  }
  .brand-sub::before, .brand-sub::after {
    content: ""; width: 22px; height: 1px; background: currentColor;
  }
  .tagline { font-size: 9.5px; }
  .front-contact {
    flex: 1;
    position: relative;
    color: var(--white);
    padding: 58px 0 0 34px;
  }
  .person-name {
    font-family: "Cinzel", serif;
    font-size: 20px;
    letter-spacing: 1px;
    position: relative;
    margin-bottom: 44px;
  }
  .contact-list { list-style: none; position: relative; font-size: 11.5px; }
  .contact-list li { display: flex; align-items: center; gap: 8px; margin-bottom: 7px; }
  .contact-list .web { margin-top: 16px; }
  .icon { width: 14px; height: 14px; flex: none; }

  /* Back */
  .card-back {
    color: var(--white);
    display: flex;
    align-items: center;
    justify-content: center;
  }
  .back-rule {
    position: absolute; left: 30px; right: 30px; top: 50%;
    height: 1px; background: var(--soft-line);
  }
  .back-lockup {
    position: relative;
    display: flex; flex-direction: column; align-items: center; gap: 8px;
    padding: 0 18px;
    background: transparent;
  }
  .back-lockup .brand-dot { background: var(--white); width: 48px; height: 48px; }
  .back-lockup .brand-name { font-size: 32px; }
  .back-lockup .brand-sub { font-size: 13px; letter-spacing: 8px; }
  .back-web { position: absolute; bottom: 26px; width: 100%; text-align: center; font-size: 11px; letter-spacing: 0.3px; }
  .rule-gap { position: absolute; left: 0; right: 0; top: 0; bottom: 0; }
</style>
</head>
<body>
  <section class="card card-front" aria-label="Business card front">
    <div class="front-brand">
      <span class="brand-dot"></span>
      <span class="brand-name">HARBORLINE</span>
      <span class="brand-sub">RENEWAL</span>
      <span class="tagline">Specializing in Water Damage Restoration</span>
    </div>
    <div class="front-contact blue-field">
      <span class="faint-ring" style="width:260px;height:260px;right:-40px;top:30px;"></span>
      <h1 class="person-name">DARNELL QUISBY</h1>
      <ul class="contact-list">
        <li>
          <svg class="icon" viewBox="0 0 14 14"><rect width="14" height="14" rx="2" fill="#fff"/><path d="M4.2 3.2l1.6 1.6-.9 1.1c.5 1.2 1.4 2.1 2.6 2.6l1.1-.9 1.6 1.6-.9 1.3C6.6 10.3 3.7 7.4 3 4.1z" fill="#1f9fd6"/></svg>
          555-318-2046
        </li>
        <li>
          <svg class="icon" viewBox="0 0 14 14"><rect width="14" height="14" rx="2" fill="#fff"/><rect x="3" y="4" width="8" height="6" fill="none" stroke="#1f9fd6" stroke-width="1"/><path d="M3 4l4 3.4L11 4" fill="none" stroke="#1f9fd6" stroke-width="1"/></svg>
          Darnell@HarborlineRenewal.example
        </li>
        <li class="web">www.HarborlineRenewal.example</li>
      </ul>
    </div>
  </section>

  <section class="card card-back blue-field" aria-label="Business card back">
    <span class="faint-ring" style="width:300px;height:300px;left:120px;top:4px;"></span>
    <div class="back-lockup">
      <span class="brand-dot"></span>
      <span class="brand-name">HARBORLINE</span>
      <span class="brand-sub">RENEWAL</span>
      <span class="tagline">Specializing in Water Damage Restoration</span>
    </div>
    <p class="back-web">www.HarborlineRenewal.example</p>
  </section>
</body>
</html>
```